Web Design Project

I need a three page website. I have designed the index.html and the specialevent.html page.

I need someone to finetune the pages for me.

Where I have difficulty is with the following:
I want to add an event table driven by php database.
The administrator of the event will login and create the wording that fits under each colmn. The administrator the submit the form to php database. The database then display in a html.

The Table contains 5 coloums and the rows can vary and can go up to as many as 100.

The table set out events on a program
In the last column of every row I need a submit button to "View and Book" I need to link those buttons with external links/pages.

I use Dreamweaver CS5 and I need to have it in this format in order for me to edit it in the future.

The Table needs to be updated once a year for this program. So ideally if someone has a password to update the certain regions this is what I have in mind.

I have also designed a mockup of the restaurant page. At the top I need.
1) 4 Colapsable panels
a) Restaurants - opening the names of the restaurants
b) Coffee shops and light lunches .... with the names
c) Family
d) Home eateries

From the colapsable panel of each of these I need a anchored link to the description/photos of each...with a BOOK now button I can submit bookings to.

I added a colapsable panel in each restaurants description to keep everything contained.

Please help

• Background must be fixed so that main.div scroll over it

The colours are chosen so please stick to it.

The green for the submit button I short is. #C8D707

I need to edit the pages in Dreamweaver CS5. /Flexilayout2pro

Please ask if you need to know anything. I exactly know what I want.

Kind regards
Pieter Vansloten

The colours are fine.

The wording " karoovistadirect BOOKING agent" should appear right at the top in the white horizon part of the background image.

The specialevent page I described already. I am interested in the editable solution. for this.

I will make up a mockup of the third page and send it later.

Regards

```html
<!DOCTYPE html>
<html lang="en">
<head>
<meta charset="utf-8">
<title>karoovistadirect – Food &amp; Drink</title>
<link rel="stylesheet" href="https://fonts.googleapis.com/css2?family=Tinos:ital,wght@0,400;1,700&family=Noto+Sans:wght@400;700&display=swap">
<style>
  :root {
    --lime: #C8D707;
    --leaf: #BDCF6C;
    --leaf-border: #8E9E45;
    --heading-green: #B3CC5C;
    --ink: #111111;
    --bar: #1a1a1a;
    --page-grey: #666666;
    --white: #ffffff;
    --rule: #555555;
    --serif: "Tinos", "Times New Roman", serif;
    --sans: "Noto Sans", Verdana, sans-serif;
  }
  * { box-sizing: border-box; margin: 0; padding: 0; }
  html, body { width: 1175px; height: 1200px; overflow: hidden; }
  body { position: relative; background: var(--page-grey); font-family: var(--sans); color: var(--ink); }

  .hero-backdrop {
    position: absolute; left: 0; top: 0; width: 1175px; height: 700px;
    background: linear-gradient(180deg, #f4f4f2 0%, #e6e5e0 5%, #b9b7ae 12%, #8f8c80 22%, #6f6e62 40%, #5b5d50 60%, #7c7a70 80%, #a29f97 100%);
  }
  .brand {
    position: absolute; left: 193px; top: 6px;
    font-family: var(--serif); font-size: 32px; font-weight: 400; color: var(--lime);
    letter-spacing: -0.3px;
  }
  .main-nav {
    position: absolute; left: 179px; top: 168px; width: 818px; height: 41px;
    background: var(--lime); border-radius: 20px;
    box-shadow: 0 2px 3px rgba(0,0,0,0.25);
  }
  .main-nav a {
    position: absolute; top: 12px; font-family: var(--serif); font-size: 13px;
    color: var(--white); text-decoration: none; text-shadow: 0 1px 1px rgba(0,0,0,0.35);
  }
  .tagline {
    position: absolute; left: 194px; top: 223px;
    font-family: var(--serif); font-style: italic; font-weight: 700; font-size: 28px;
    color: var(--white); text-shadow: 0 1px 2px rgba(0,0,0,0.4);
  }

  .content-panel {
    position: absolute; left: 179px; top: 281px; width: 818px; height: 911px;
    background: var(--white); border-radius: 16px;
  }
  .page-title {
    position: absolute; left: 12px; top: 14px; width: 791px; height: 37px;
    background: var(--bar); border-radius: 8px 8px 0 0;
    color: var(--white); font-size: 26px; font-weight: 400; line-height: 40px; padding-left: 14px;
  }
  .restaurants-title {
    position: absolute; left: 24px; top: 70px; font-size: 19px; font-weight: 400;
  }
  .rule { position: absolute; height: 1px; background: var(--rule); }
  .restaurant-list {
    position: absolute; left: 22px; top: 111px; list-style: none; font-size: 14.5px; line-height: 18.7px;
  }

  .category-grid {
    position: absolute; left: 12px; top: 208px; width: 791px; height: 248px; background: var(--leaf);
  }
  .category-card {
    position: absolute; width: 376px; height: 103px; background: var(--white);
    border: 3px solid var(--leaf-border); padding: 4px 10px 0 10px;
  }
  .category-card h3 { font-size: 17.5px; font-weight: 400; line-height: 22px; }
  .category-card p { font-size: 11.8px; line-height: 14.8px; letter-spacing: 0.35px; margin-top: 2px; padding-right: 10px; }

  .venue-title {
    position: absolute; left: 14px; font-size: 19px; font-weight: 700; color: var(--heading-green); letter-spacing: 0.3px;
  }
  .venue-photo { position: absolute; width: 93px; height: 62px; }
  .photo-meadow { background: linear-gradient(180deg, #6f95c8 0%, #b8c8d8 35%, #7b8a5c 50%, #c8c23a 70%, #b4b02c 100%); }
  .photo-bridge { background: linear-gradient(180deg, #4c4a32 0%, #6e6a46 35%, #8f8a78 60%, #5d5a50 100%); }
  .venue-text {
    position: absolute; left: 338px; width: 430px; font-size: 11.8px; line-height: 14.4px; letter-spacing: 0.35px;
  }
  .read-more {
    position: absolute; left: 700px; width: 99px; height: 27px; border-radius: 3px;
    background: linear-gradient(180deg, #c8d707 0%, #a4b106 55%, #8d9a05 100%);
    border: 1px solid #7d8805; color: var(--ink); font-family: var(--sans); font-size: 14.5px;
    text-align: center; line-height: 25px;
  }
</style>
</head>
<body>
  <div class="hero-backdrop" role="img" aria-label="Sepia photograph of a Karoo valley with mountains and a small town with white houses"></div>

  <header>
    <div class="brand">karoovistadirect</div>
    <nav class="main-nav">
      <a href="#" style="left:262px">Home</a>
      <a href="#" style="left:324px">Accommodation</a>
      <a href="#" style="left:446px">Play</a>
      <a href="#" style="left:518px">Contact</a>
    </nav>
    <div class="tagline">Your booking agent for</div>
  </header>

  <main class="content-panel">
    <h1 class="page-title">Food &amp; Drink</h1>

    <h2 class="restaurants-title">Restaurants</h2>
    <div class="rule" style="left:12px; top:103px; width:790px;"></div>
    <ol class="restaurant-list">
      <li>1. Saffron Table</li>
      <li>2. Fig Tree Bistro</li>
      <li>3. Studio Cafe</li>
      <li>4. Veld Kitchen</li>
    </ol>

    <section class="category-grid">
      <article class="category-card" style="left:13px; top:17px;">
        <h3>Coffe shops and Lunch</h3>
        <p>Lorem Ipsum is simply dummy text of the printing and typesetting industry. Lorem Ipsum has been the industry's standard dummy text ever since the 1500s, when</p>
      </article>
      <article class="category-card" style="left:401px; top:17px;">
        <h3>Home Eateries</h3>
        <p>Lorem Ipsum is simply dummy text of the printing and typesetting industry. Lorem Ipsum has been the industry's standard dummy text ever since the 1500s, when</p>
      </article>
      <article class="category-card" style="left:13px; top:133px;">
        <h3>Coffe shops and Lunch</h3>
        <p>Lorem Ipsum is simply dummy text of the printing and typesetting industry. Lorem Ipsum has been the industry's standard dummy text ever since the 1500s, when</p>
      </article>
      <article class="category-card" style="left:401px; top:133px;">
        <h3>Take aways</h3>
        <p>Lorem Ipsum is simply dummy text of the printing and typesetting industry. Lorem Ipsum has been the industry's standard dummy text ever since the 1500s, when</p>
      </article>
    </section>

    <section class="venue">
      <h2 class="venue-title" style="top:494px;">Saffron Table</h2>
      <div class="rule" style="left:12px; top:524px; width:794px;"></div>
      <div class="venue-photo photo-meadow" role="img" aria-label="Meadow with yellow flowers under a cloudy sky" style="left:30px; top:538px;"></div>
      <div class="venue-photo photo-bridge" role="img" aria-label="Stone arch bridge beneath a large tree" style="left:136px; top:538px;"></div>
      <div class="venue-photo photo-bridge" role="img" aria-label="Stone arch bridge beneath a large tree" style="left:242px; top:538px;"></div>
      <div class="venue-photo photo-meadow" role="img" aria-label="Meadow with yellow flowers under a cloudy sky" style="left:30px; top:611px;"></div>
      <div class="venue-photo photo-bridge" role="img" aria-label="Stone arch bridge beneath a large tree" style="left:136px; top:611px;"></div>
      <div class="venue-photo photo-bridge" role="img" aria-label="Stone arch bridge beneath a large tree" style="left:242px; top:611px;"></div>
      <p class="venue-text" style="top:537px;">Lorem Ipsum is simply dummy text of the printing and typesetting industry. Lorem Ipsum has been the industry's standard dummy text ever since the 1500s, when an unknown printer took a galley of type and scrambled it to make a type specimen book. It has survived not only five centuries, but also the leap into electronic typesetting, re-maining essentially unchanged. It was popularised in the 1960s with the release of Lettrafix sheets containing.</p>
      <a class="read-more" href="#" style="top:647px;">Read More</a>
    </section>

    <section class="venue">
      <h2 class="venue-title" style="top:707px;">Saffron Table</h2>
      <div class="rule" style="left:12px; top:737px; width:794px;"></div>
      <div class="venue-photo photo-meadow" role="img" aria-label="Meadow with yellow flowers under a cloudy sky" style="left:30px; top:751px;"></div>
      <div class="venue-photo photo-bridge" role="img" aria-label="Stone arch bridge beneath a large tree" style="left:136px; top:751px;"></div>
      <div class="venue-photo photo-bridge" role="img" aria-label="Stone arch bridge beneath a large tree" style="left:242px; top:751px;"></div>
      <div class="venue-photo photo-meadow" role="img" aria-label="Meadow with yellow flowers under a cloudy sky" style="left:30px; top:824px;"></div>
      <div class="venue-photo photo-bridge" role="img" aria-label="Stone arch bridge beneath a large tree" style="left:136px; top:824px;"></div>
      <div class="venue-photo photo-bridge" role="img" aria-label="Stone arch bridge beneath a large tree" style="left:242px; top:824px;"></div>
      <p class="venue-text" style="top:750px;">Lorem Ipsum is simply dummy text of the printing and typesetting industry. Lorem Ipsum has been the industry's standard dummy text ever since the 1500s, when an unknown printer took a galley of type and scrambled it to make a type specimen book. It has survived not only five centuries, but also the leap into electronic typesetting, re-maining essentially unchanged. It was popularised in the 1960s with the release of Lettrafix sheets containing.</p>
      <a class="read-more" href="#" style="top:860px;">Read More</a>
    </section>
  </main>
</body>
</html>
```